A new presentation to our clients

we are a Real Estate agency, our website is www.lumibrasa.com and it’s time to have a new, fashion and remarcable Business Card. we want to differentiate ourselves from other companies so we want a business card that differentiates us. we want the business card to impact our customers. in the competitive market that we have today, we have to be different and it is this difference that we seek

Target Market(s)

Real Estate Clients

Contact Information for Business Card

We search a totaly diferent card from the usual

Font styles to use
Sans Serif

Colors
e34197

Requirements
Must have
• Logo, adress, phone contact, e-mail, photo, and our website
Nice to have
• We would like to see a modern business card
Should not have
• Houses or building draws

```html
<!DOCTYPE html>
<html lang="en">
<head>
<meta charset="utf-8">
<title>Lumi Brasa — Business Card</title>
<link rel="stylesheet" href="https://fonts.googleapis.com/css2?family=Work+Sans:wght@400;500;600&display=swap">
<style>
  :root {
    --bg: #1e1e1f;
    --card: #262627;
    --card-edge: #1b1b1c;
    --pink: #ec1a7f;
    --white: #f2f2f2;
  }
  * { box-sizing: border-box; margin: 0; padding: 0; }
  html, body { width: 1200px; height: 900px; overflow: hidden; }
  body {
    background: var(--bg);
    font-family: "Work Sans", Arial, sans-serif;
    position: relative;
  }
  .card {
    position: absolute;
    left: 250px;
    width: 700px;
    height: 385px;
    background: linear-gradient(135deg, var(--card-edge) 0%, var(--card) 55%, #2e2e2f 100%);
    border-bottom: 7px solid var(--pink);
    box-shadow: 0 10px 30px rgba(0,0,0,.45);
  }
  .card--front { top: 45px; }
  .card--back { top: 470px; }
  .brand-name {
    color: var(--pink);
    font-weight: 500;
    letter-spacing: 1px;
    white-space: nowrap;
  }
  .card--front .brand-name {
    position: absolute;
    left: 0; right: 0; top: 150px;
    text-align: center;
    font-size: 62px;
  }
  .card--back .brand-name {
    position: absolute;
    left: 40px; top: 150px;
    font-size: 48px;
  }
  .divider {
    position: absolute;
    left: 350px; top: 85px;
    width: 2px; height: 195px;
    background: var(--white);
  }
  .contact {
    position: absolute;
    left: 375px; top: 80px;
    color: var(--white);
  }
  .contact__name {
    color: var(--pink);
    font-size: 27px;
    font-weight: 500;
    line-height: 1;
  }
  .contact__role { font-size: 17px; margin: 4px 0 10px; }
  .contact__list { list-style: none; font-size: 18px; line-height: 26px; }
  .contact__list li { display: flex; align-items: center; gap: 9px; }
  .contact__list svg { width: 12px; height: 12px; fill: var(--pink); flex: none; }
  .contact__address { font-size: 18px; line-height: 26px; margin-top: 4px; }
</style>
</head>
<body>
  <section class="card card--front">
    <div class="brand-name">Lumi Brasa</div>
  </section>

  <section class="card card--back">
    <div class="brand-name">Lumi Brasa</div>
    <div class="divider"></div>
    <div class="contact">
      <div class="contact__name">DANIEL REIS</div>
      <div class="contact__role">Director</div>
      <ul class="contact__list">
        <li><svg viewBox="0 0 12 12"><path d="M2.5 0.5 L4.5 0.5 L5.2 3 L3.8 4.2 Q5 7 7.8 8.2 L9 6.8 L11.5 7.5 L11.5 9.5 Q11.5 11.5 9.5 11.5 Q1 10.5 0.5 2.5 Q0.5 0.5 2.5 0.5Z"/></svg>(+351) 220 481 356</li>
        <li><svg viewBox="0 0 12 12"><rect x="3" y="0.5" width="6" height="3"/><rect x="0.5" y="4" width="11" height="5" rx="1"/><rect x="3" y="8" width="6" height="3.5"/></svg>(+351) 220 481 357</li>
        <li><svg viewBox="0 0 12 12"><path d="M0.5 2 H11.5 V10 H0.5Z M1.5 3 V9 H10.5 V3 L6 6.5Z" fill-rule="evenodd"/></svg>geral@lumibrasa.com</li>
        <li><svg viewBox="0 0 12 12"><circle cx="6" cy="6" r="5.5"/><path d="M0.5 6 H11.5 M6 0.5 V11.5" stroke="#262627" stroke-width="1"/></svg>www.lumibrasa.com</li>
      </ul>
      <p class="contact__address">Rua das Camélias, 148<br>4150-082, Porto Norte</p>
    </div>
  </section>
</body>
</html>
```